Redesign website for small print company

Vindurgata is a small printing company in Iceland mainly servicing Students, schools, etc. We are also doing all kind of other jobs, like business cards, book printing, brochure printing etc. We are also selling books online.
Our website is: www.vindurgata.is
What we are looking for is:
- Web Design (Uncoded - PSD layout only)
- Mobile friendly design, using our current color scheme: Red, green, yellow and light gray.
- Clean simple design
- Simple, light and easy to use.
- More menu Items/drop down
Industry/Entity Type
Digital Printing
Number of Pages Required
5+ page
Requirements
Must have
- Easy navigation
- Designed for mobile
- Current color scheme (see logo)
Nice to have
- Icon based products

```html
<!DOCTYPE html>
<html lang="en">
<head>
<meta charset="utf-8">
<title>Vindurgata – Printing for students and schools</title>
<link href="https://fonts.googleapis.com/css2?family=Montserrat:wght@400;500;600;700;800&family=Jost:wght@400;500&display=swap" rel="stylesheet">
<style>
:root{
  --red:#e3221b;
  --green:#0b5e2f;
  --yellow:#f3c500;
  --yellow-soft:#fbeeb8;
  --gray-light:#f3f3f3;
  --gray-mid:#e4e4e4;
  --ink:#2b2b2b;
  --text:#555;
  --dark:#2e2e2e;
  --darker:#1f1f1f;
  --white:#fff;
}
*{box-sizing:border-box;margin:0;padding:0}
html,body{width:1200px;height:3689px;overflow:hidden}
body{position:relative;background:var(--white);font-family:'Jost',sans-serif;color:var(--text)}
.abs{position:absolute}
.heading{font-family:'Montserrat',sans-serif;font-weight:700;font-size:26px;text-align:center;color:var(--ink);letter-spacing:.5px;text-transform:uppercase;width:1200px;left:0}
.heading .accent{color:var(--red)}
.btn{position:absolute;background:var(--green);color:var(--white);font-family:'Montserrat',sans-serif;font-weight:700;font-size:13px;letter-spacing:.5px;display:flex;align-items:center;justify-content:center;border-radius:3px;text-transform:uppercase}

/* top bar */
.topbar{top:0;left:0;width:1200px;height:34px;background:var(--dark);color:#ddd;font-size:12px;font-family:'Montserrat',sans-serif}
.topbar .lang{left:144px;top:10px}
.topbar .flag{left:226px;top:11px;width:22px;height:13px;background:linear-gradient(#b22 0 50%,#fff 50% 60%,#b22 60%);border-radius:1px}
.topbar .flag::before{content:"";position:absolute;left:0;top:0;width:10px;height:7px;background:#3b3b8f}
.topbar .info{top:10px;display:flex;gap:6px;align-items:center}

/* header */
.header{top:34px;left:0;width:1200px;height:89px;background:var(--white)}
.brand{left:140px;top:26px;display:flex;align-items:center;gap:10px}
.brand .mark{width:36px;height:36px;background:var(--red)}
.brand .name{font-family:'Montserrat',sans-serif;font-weight:800;font-size:27px;color:var(--ink);letter-spacing:.5px}
.nav{left:586px;top:38px;display:flex;gap:40px;font-family:'Montserrat',sans-serif;font-weight:700;font-size:13px;color:var(--ink)}
.nav .active{color:var(--red)}
.cart{left:1020px;top:30px;width:34px;height:34px;border:2px solid var(--green);border-radius:50%}

/* hero */
.hero{top:123px;left:0;width:1200px;height:475px;background:linear-gradient(90deg,#d8d8d8,#cfcfcf)}
.hero h1{left:150px;top:104px;font-family:'Montserrat',sans-serif;font-weight:400;font-size:40px;line-height:49px;color:#333;white-space:nowrap}
.hero h1 b{font-weight:800}
.hero .rule{left:150px;top:258px;width:480px;height:2px;background:#333}
.hero .dots{left:150px;top:380px;display:flex;gap:5px}
.hero .dots span{width:9px;height:9px;border-radius:50%;background:#666}
.hero .dots span:first-child{background:var(--red)}
.rollup{position:absolute;top:40px;width:150px;height:380px}
.rollup .stand{position:absolute;bottom:0;left:-6px;width:162px;height:14px;background:#888;border-radius:3px}

/* products */
.product{position:absolute;width:283px;height:197px;background:var(--gray-light);display:flex;flex-direction:column;align-items:center;padding-top:38px}
.product.featured{background:var(--white);border:1px solid #e6e6e6;box-shadow:0 3px 14px rgba(0,0,0,.12)}
.product .ico{width:80px;height:80px;border-radius:50%;background:var(--yellow-soft);display:flex;align-items:center;justify-content:center}
.product .label{margin-top:22px;font-family:'Montserrat',sans-serif;font-weight:700;font-size:17px;color:var(--ink)}

/* about */
.about{top:1217px;left:0;width:1200px;height:517px;background:var(--gray-light)}
.about .kicker{left:642px;top:62px;font-family:'Montserrat',sans-serif;font-weight:700;font-size:20px;color:var(--red)}
.about h2{left:642px;top:92px;font-family:'Montserrat',sans-serif;font-weight:700;font-size:24px;color:var(--ink)}
.about .copy{left:642px;top:136px;width:515px;font-size:13.5px;line-height:21px}
.about .copy p{margin-bottom:12px}

/* steps */
.step{position:absolute;width:240px;text-align:center}
.step .title{font-family:'Montserrat',sans-serif;font-weight:700;font-size:15px;color:var(--ink);margin-top:12px}
.step .desc{font-size:13px;line-height:18px;margin-top:4px;color:#444}

/* offers */
.offers{top:2193px;left:0;width:1200px;height:504px;background:linear-gradient(135deg,#f7d400,#e9b800 60%,#f4cd00)}
.offer{position:absolute;top:121px;height:307px;overflow:hidden}

/* reviews */
.review{position:absolute;top:2813px;width:289px;height:170px;background:var(--gray-light);padding:24px 22px}
.review .top{display:flex;justify-content:space-between;font-family:'Montserrat',sans-serif;font-weight:600;font-size:13px;color:var(--ink)}
.review .stars{color:#f5a700;letter-spacing:1px;font-size:14px}
.review p{margin-top:12px;font-size:12.5px;line-height:18px;color:#555}
.reviewer{position:absolute;top:3003px;display:flex;align-items:center;gap:14px}
.reviewer .avatar{width:52px;height:52px;border-radius:50%;background:linear-gradient(#c9c3bd,#8d8780)}
.reviewer .who{font-family:'Montserrat',sans-serif;font-weight:700;font-size:13px;color:var(--red)}
.reviewer .who span{display:block;font-family:'Jost',sans-serif;font-weight:400;color:#444;font-size:12px}

/* perks band */
.perks{top:3192px;left:0;width:1200px;height:120px;background:var(--green);color:var(--white)}
.perk{position:absolute;top:30px;display:flex;align-items:center;gap:14px}
.perk .circle{width:58px;height:58px;border-radius:50%;background:var(--white);display:flex;align-items:center;justify-content:center}
.perk b{display:block;font-family:'Montserrat',sans-serif;font-size:14px;letter-spacing:.3px}
.perk span{font-size:13px}

/* footer */
.footer{top:3312px;left:0;width:1200px;height:327px;background:var(--dark);color:#ccc}
.signup{left:140px;top:49px;width:335px;height:244px;background:var(--white);padding:30px 24px}
.signup h3{font-family:'Montserrat',sans-serif;font-weight:800;font-size:20px;color:var(--red)}
.signup h3 span{color:var(--ink)}
.signup p{font-size:12.5px;line-height:17px;color:#555;margin-top:6px}
.signup .field{margin-top:14px;height:38px;border:1px solid #ccc;font-size:12px;color:#999;padding:11px 12px}
.fcol{position:absolute;top:78px;font-size:12.5px;line-height:22px}
.fcol h4{font-family:'Montserrat',sans-serif;font-weight:700;font-size:13px;color:var(--white);margin-bottom:6px;letter-spacing:.3px}
.fcol li{list-style:none}
.fcol li::before{content:"› ";color:#999}
.cards{display:flex;gap:5px;margin-top:4px}
.cards span{width:36px;height:22px;background:#e6e6e6;border-radius:3px}
.socials{left:916px;top:268px;display:flex;gap:7px}
.socials span{width:22px;height:22px;border-radius:50%;background:#4a7fc1}
.socials span:nth-child(4){background:#d34836}
.socials span:nth-child(5){background:#b5576b}
.bottombar{top:3639px;left:0;width:1200px;height:50px;background:var(--darker);color:#aaa;font-size:12px;padding:18px 140px}
</style>
</head>
<body>

<!-- top bar -->
<div class="abs topbar">
  <div class="abs lang">LANGUAGE</div>
  <div class="abs flag"></div>
  <div class="abs info" style="left:728px">
    <svg width="12" height="12" viewBox="0 0 24 24"><path fill="#ddd" d="M6.6 10.8a15 15 0 006.6 6.6l2.2-2.2a1 1 0 011-.25 11 11 0 003.6.6 1 1 0 011 1V20a1 1 0 01-1 1A17 17 0 013 4a1 1 0 011-1h3.5a1 1 0 011 1 11 11 0 00.6 3.6 1 1 0 01-.25 1z"/></svg>555 0142</div>
  <div class="abs info" style="left:816px">
    <svg width="13" height="10" viewBox="0 0 26 20"><rect width="26" height="20" rx="2" fill="#ddd"/><path d="M1 2l12 9 12-9" stroke="#2e2e2e" stroke-width="2" fill="none"/></svg>verk@vindurgata.is</div>
  <div class="abs info" style="left:964px">
    <svg width="12" height="12" viewBox="0 0 24 24"><circle cx="12" cy="12" r="10" stroke="#ddd" stroke-width="2.5" fill="none"/><path d="M12 6v6l4 3" stroke="#ddd" stroke-width="2.5" fill="none"/></svg>Mon - Fri: 9-17</div>
</div>

<!-- header -->
<header class="abs header">
  <div class="abs brand"><span class="mark"></span><span class="name">VINDURGATA</span></div>
  <nav class="abs nav"><span class="active">HOME</span><span>SERVICES</span><span>JOB SUBMIT</span><span>ABOUT US</span></nav>
  <svg class="abs" style="left:988px;top:40px" width="16" height="16" viewBox="0 0 24 24"><circle cx="10" cy="10" r="7" stroke="#2b2b2b" stroke-width="3" fill="none"/><path d="M15 15l7 7" stroke="#2b2b2b" stroke-width="3"/></svg>
  <div class="abs cart">
    <svg style="position:absolute;left:7px;top:8px" width="17" height="15" viewBox="0 0 24 20"><path d="M1 2h4l3 11h12l3-8H7" stroke="#e3221b" stroke-width="2.5" fill="none"/><circle cx="9" cy="17" r="2" fill="#e3221b"/><circle cx="19" cy="17" r="2" fill="#e3221b"/></svg>
  </div>
</header>

<!-- hero -->
<section class="abs hero">
  <h1 class="abs">Beautiful is when the<br><b>Graphics</b> on your roll-up<br>Is clearer than <b>REALITY.</b></h1>
  <div class="abs rule"></div>
  <div class="btn" style="left:150px;top:302px;width:162px;height:50px;font-size:14px">ORDER NOW</div>
  <div class="abs dots"><span></span><span></span><span></span></div>
  <div class="rollup" style="left:670px">
    <div role="img" aria-label="Roll-up banner promoting a food product" style="position:absolute;inset:0 0 14px;background:linear-gradient(#f0ece6 0 22%,#c8171b 22% 80%,#8f0f13 80%)"></div>
    <div class="stand"></div>
  </div>
  <div class="rollup" style="left:890px">
    <div role="img" aria-label="Roll-up banner promoting a shopping voucher with a smiling couple" style="position:absolute;inset:0 0 14px;background:linear-gradient(#f4f4f4 0 10%,#3a7ad1 10% 62%,#1b2f8c 62%)"></div>
    <div class="stand"></div>
  </div>
</section>

<!-- products -->
<h2 class="abs heading" style="top:662px"><span class="accent">OUR</span> PRODUCTS</h2>
<div class="product featured" style="left:140px;top:720px">
  <div class="ico"><svg width="34" height="40" viewBox="0 0 34 40"><rect x="3" y="3" width="20" height="30" stroke="#e3221b" stroke-width="2.5" fill="none"/><path d="M8 10h10M8 16h10M8 22h6" stroke="#e3221b" stroke-width="2"/><path d="M26 8l5 3-7 22-5-3z" stroke="#e3221b" stroke-width="2" fill="#fff"/></svg></div>
  <div class="label">ESSAYS</div>
</div>
<div class="product" style="left:457px;top:720px">
  <div class="ico"><svg width="40" height="30" viewBox="0 0 40 30"><rect x="2" y="2" width="36" height="26" rx="2" stroke="#e3221b" stroke-width="2.5" fill="none"/><circle cx="13" cy="12" r="4" stroke="#e3221b" stroke-width="2" fill="none"/><path d="M7 22c1-4 11-4 12 0M23 11h10M23 16h10M23 21h7" stroke="#e3221b" stroke-width="2" fill="none"/></svg></div>
  <div class="label">BUSINESS CARDS</div>
</div>
<div class="product" style="left:775px;top:720px">
  <div class="ico"><svg width="40" height="32" viewBox="0 0 40 32"><path d="M2 4l12-2v26L2 30zM14 2l12 4v24l-12-2zM26 6l12-2v24l-12 2z" stroke="#e3221b" stroke-width="2.5" fill="none"/><path d="M5 10h6M17 10h6M29 12h6M5 16h6M17 16h6M29 18h6" stroke="#e3221b" stroke-width="2"/></svg></div>
  <div class="label">LEAFLETS</div>
</div>
<div class="product" style="left:140px;top:952px">
  <div class="ico"><svg width="34" height="40" viewBox="0 0 34 40"><rect x="3" y="6" width="24" height="30" rx="2" stroke="#e3221b" stroke-width="2.5" fill="none"/><path d="M8 2h20a3 3 0 013 3v27" stroke="#e3221b" stroke-width="2.5" fill="none"/><path d="M8 14h14M8 20h14M8 26h9" stroke="#e3221b" stroke-width="2"/></svg></div>
  <div class="label">BOOK PRINTING</div>
</div>
<div class="product" style="left:457px;top:952px">
  <div class="ico"><svg width="32" height="40" viewBox="0 0 32 40"><rect x="3" y="3" width="26" height="34" stroke="#e3221b" stroke-width="2.5" fill="none"/><rect x="8" y="9" width="16" height="12" fill="#e3221b"/><path d="M8 27h16M8 32h10" stroke="#e3221b" stroke-width="2"/></svg></div>
  <div class="label">POSTERS</div>
</div>
<div class="product" style="left:775px;top:952px">
  <div class="ico"><svg width="34" height="40" viewBox="0 0 34 40"><rect x="4" y="3" width="26" height="34" rx="2" stroke="#e3221b" stroke-width="2.5" fill="none"/><path d="M10 3v34" stroke="#e3221b" stroke-width="2"/><rect x="14" y="10" width="11" height="7" stroke="#e3221b" stroke-width="2" fill="none"/></svg></div>
  <div class="label">TEXTBOOKS</div>
</div>

<!-- about -->
<section class="abs about">
  <div role="img" aria-label="Designers working at a desk with laptops and printed layouts" class="abs" style="left:140px;top:69px;width:362px;height:300px;background:linear-gradient(135deg,#e8e6e2,#b9bcc0 55%,#6f7378)"></div>
  <div role="img" aria-label="Colour swatch guide and a magnifying loupe" class="abs" style="left:340px;top:248px;width:258px;height:200px;border:6px solid var(--gray-light);background:linear-gradient(120deg,#e6c12b,#d23b6a 40%,#3c6ec9 70%,#2a2a2a)"></div>
  <div class="abs kicker">ABOUT US</div>
  <h2 class="abs">WELCOME TO UNIVERSITY</h2>
  <div class="abs copy">
    <p>University education is a company located in the campus, which has specialized in the service of school staff, as well as providing general public printing.</p>
    <p>Higher education publishes seminars and first-class textbooks for courses, prints theses for lesson, as well as working on an unprecedented number of smaller pieces for students, teachers and organizations. These include brochures, reports, questionnaires, business cards, books, OCR scanning and more.</p>
    <p>Higher education is a tailored print shop, The Lark is the official eco-label of the Nordic countries, which has created a foothold in this country and is known among consumers.</p>
  </div>
  <div class="btn" style="left:642px;top:408px;width:126px;height:38px;font-size:12px">READ MORE</div>
</section>

<!-- how it works -->
<h2 class="abs heading" style="top:1801px"><span class="accent">HOW WE MAKE</span> PRINTING AS EASY</h2>
<svg class="abs" style="left:0;top:1840px" width="1200" height="160" viewBox="0 0 1200 160">
  <g fill="none" stroke-width="3" stroke="#0b5e2f">
    <path d="M228.5 104.8 A58 58 0 1 1 263.2 139.5"/>
    <path d="M547.5 104.8 A58 58 0 1 1 582.2 139.5"/>
    <path d="M874.5 104.8 A58 58 0 1 1 909.2 139.5"/>
  </g>
  <g fill="none" stroke="#aaa" stroke-width="2">
    <path d="M400 80q35-20 70-5"/><path d="M462 70l8 5-10 3"/>
    <path d="M722 80q40-20 80-5"/><path d="M794 70l8 5-10 3"/>
  </g>
  <g transform="translate(3 5)">
    <g stroke="#e3221b" stroke-width="3" fill="none">
      <path d="M278 95V58a5 5 0 0110 0v22h6a5 5 0 015 5v18c0 6-6 10-12 10h-6c-5 0-8-3-10-6l-8-14a4 4 0 016-5z"/>
      <path d="M270 52a14 14 0 0126 0"/>
    </g>
  </g>
  <g transform="translate(59 13)">
    <g stroke="#e3221b" stroke-width="3" fill="none">
      <rect x="523" y="47" width="40" height="50" rx="3"/>
      <path d="M531 60h22M531 68h22M531 76h14"/>
    </g>
    <circle cx="564" cy="93" r="8" fill="#e3221b"/>
  </g>
  <g transform="translate(17 8)">
    <g stroke="#e3221b" stroke-width="3" fill="none">
      <path d="M888 60h8l7 28h28l6-20h-37"/>
      <path d="M915 50l5 6 10-12"/>
    </g>
    <circle cx="907" cy="95" r="4" fill="#e3221b"/><circle cx="928" cy="95" r="4" fill="#e3221b"/>
  </g>
  <g font-family="Montserrat,sans-serif" font-weight="800" font-size="15" text-anchor="middle">
    <circle cx="230" cy="122" r="14" fill="#f3c500"/><text x="230" y="127" fill="#2b2b2b">1</text>
    <circle cx="549" cy="122" r="14" fill="#f3c500"/><text x="549" y="127" fill="#2b2b2b">2</text>
    <circle cx="876" cy="122" r="14" fill="#f3c500"/><text x="876" y="127" fill="#2b2b2b">3</text>
  </g>
</svg>
<div class="step" style="left:163px;top:1993px"><div class="title">SELECT OPTIONS</div><div class="desc">Lorem ipsum dolor sit amet contuer adiping elit sed diam noummy.</div></div>
<div class="step" style="left:482px;top:1993px"><div class="title">UPLOAD YOUR DESIGN</div><div class="desc">Lorem ipsum dolor sit amet contuer adiping elit sed diam noummy.</div></div>
<div class="step" style="left:809px;top:1993px"><div class="title">CHECKOUT &amp; ORDER</div><div class="desc">Lorem ipsum dolor sit amet contuer adiping elit sed diam noummy.</div></div>
<div class="btn" style="left:537px;top:2083px;width:126px;height:38px;font-size:12px">GET STARTED</div>

<!-- offers -->
<section class="abs offers">
  <h2 class="abs heading" style="top:65px"><span class="accent">OFFERS</span> AND DEALS</h2>
  <div class="offer" style="left:140px;width:445px;background:#f1f1f1">
    <div role="img" aria-label="Stack of colourful printed business cards" class="abs" style="left:232px;top:100px;width:180px;height:108px;background:linear-gradient(135deg,#f7f7f7,#e3221b 45%,#2f7fd0 75%,#f2c40d);transform:rotate(-18deg);box-shadow:0 10px 18px rgba(0,0,0,.25)"></div>
    <div class="abs" style="left:24px;top:48px;font-family:'Montserrat',sans-serif;font-weight:800;font-size:34px;line-height:38px;color:var(--red)">25% OFF</div>
    <div class="abs" style="left:24px;top:86px;font-family:'Montserrat',sans-serif;font-weight:800;font-size:34px;line-height:38px;color:var(--ink)">GET YOUR</div>
    <div class="abs" style="left:24px;top:128px;font-family:'Montserrat',sans-serif;font-weight:500;font-size:22px;line-height:28px;color:#444">CUSTOMIZED<br>ESSAYS</div>
    <div class="btn" style="left:24px;top:194px;width:106px;height:38px;font-size:12px">GET NOW</div>
  </div>
  <div class="offer" style="left:615px;width:442px">
    <div role="img" aria-label="Fanned printed book covers in purple and orange tones" class="abs" style="inset:0;background:linear-gradient(135deg,#4b2a5e,#8a3f7a 45%,#c96a3a 75%,#3d2c55)"></div>
    <div class="abs" style="left:45px;top:64px;width:352px;height:175px;background:rgba(40,20,40,.55)"></div>
    <div class="abs" style="left:0;width:442px;top:84px;text-align:center;font-family:'Montserrat',sans-serif;font-weight:800;font-size:30px;color:var(--white)">GET YOUR</div>
    <div class="abs" style="left:0;width:442px;top:126px;text-align:center;font-family:'Montserrat',sans-serif;font-weight:500;font-size:18px;color:var(--white)">CUSTOMIZED BOOK PRINTING</div>
    <div class="btn" style="left:168px;top:170px;width:106px;height:38px;font-size:12px">GET NOW</div>
  </div>
</section>

<!-- reviews -->
<h2 class="abs heading" style="top:2755px"><span class="accent">CLIENT</span> REVIEWS</h2>
<svg class="abs" style="left:92px;top:2885px" width="14" height="30"><path d="M12 2L3 15l9 13" stroke="#ccc" stroke-width="2" fill="none"/></svg>
<svg class="abs" style="left:1094px;top:2885px" width="14" height="30"><path d="M2 2l9 13-9 13" stroke="#ccc" stroke-width="2" fill="none"/></svg>
<div class="review" style="left:140px"><div class="top">Lorem ipsum dolor<span class="stars">★★★★★</span></div><p>Lorem ipsum dolor sit amet consetuer adipcing elit sed diam nonummy nibh euismod tidunt ut laoreet dolore magna aliquam erat volut. Ut wisi enim ad minim veniam.</p></div>
<div class="review" style="left:457px"><div class="top">Lorem ipsum dolor<span class="stars">★★★★★</span></div><p>Lorem ipsum dolor sit amet consetuer adipcing elit sed diam nonummy nibh euismod tidunt ut laoreet dolore magna aliquam erat volut. Ut wisi enim ad minim veniam.</p></div>
<div class="review" style="left:770px"><div class="top">Lorem ipsum dolor<span class="stars">★★★★★</span></div><p>Lorem ipsum dolor sit amet consetuer adipcing elit sed diam nonummy nibh euismod tidunt ut laoreet dolore magna aliquam erat volut. Ut wisi enim ad minim veniam.</p></div>
<div class="reviewer" style="left:162px"><div class="avatar" role="img" aria-label="Client portrait"></div><div class="who">Ari Jónsson<span>(Lorem Ipsum)</span></div></div>
<div class="reviewer" style="left:478px"><div class="avatar" role="img" aria-label="Client portrait"></div><div class="who">Sara Mist<span>(Lorem Ipsum)</span></div></div>
<div class="reviewer" style="left:792px"><div class="avatar" role="img" aria-label="Client portrait"></div><div class="who">Eva Pálsdóttir<span>(Lorem Ipsum)</span></div></div>
<div class="btn" style="left:537px;top:3088px;width:126px;height:38px;font-size:12px">VIEW ALL</div>

<!-- perks -->
<section class="abs perks">
  <div class="perk" style="left:143px"><div class="circle"><svg width="30" height="22" viewBox="0 0 30 22"><rect x="1" y="3" width="17" height="12" fill="#0b5e2f"/><path d="M18 7h6l4 4v4H18z" fill="#0b5e2f"/><circle cx="7" cy="17" r="3" fill="#0b5e2f"/><circle cx="23" cy="17" r="3" fill="#0b5e2f"/></svg></div><div><b>FREE SHIPPING &amp; RETURN</b><span>Free shipping on all orders over $99.</span></div></div>
  <div class="perk" style="left:497px"><div class="circle"><svg width="34" height="34" viewBox="0 0 34 34"><circle cx="17" cy="17" r="14" stroke="#0b5e2f" stroke-width="2.5" fill="none"/><text x="17" y="24" text-anchor="middle" font-family="Montserrat,sans-serif" font-weight="800" font-size="19" fill="#0b5e2f">$</text></svg></div><div><b>MONEY BACK GUARANTEE</b><span>100% money back guarantee.</span></div></div>
  <div class="perk" style="left:827px"><div class="circle"><svg width="34" height="34" viewBox="0 0 34 34"><circle cx="17" cy="17" r="13" stroke="#0b5e2f" stroke-width="2.5" fill="none"/><path d="M17 9v8l5 4" stroke="#0b5e2f" stroke-width="2.5" fill="none"/></svg></div><div><b>ONLINE SUPPORT 24/7</b><span>Lorem ipsum dolor sit amet.</span></div></div>
</section>

<!-- footer -->
<footer class="abs footer">
  <div class="abs signup">
    <h3>SIGN UP <span>TODAY !</span></h3>
    <p>Lorem ipsum dolor sit laoreet dolore magnitutpat quis nostrud exerci tation.</p>
    <div class="field">Your Email Address...</div>
    <div class="btn" style="left:24px;top:180px;width:116px;height:34px;font-size:12px">SUBSCRIBE!</div>
  </div>
  <div class="fcol" style="left:510px;top:76px"><h4>QUICK LINKS</h4><ul><li>Home</li><li>Services</li><li>Job Submit</li><li>About Us</li></ul>
    <h4 style="margin-top:12px">PAYMENTS OPTIONS</h4><div class="cards"><span></span><span></span><span></span><span></span><span></span></div></div>
  <div class="fcol" style="left:730px;top:76px"><h4>CAN WE HELP YOU?</h4><ul><li>Your Account</li><li>Shipping &amp; Handling</li><li>Refunds &amp; Returns</li><li>Stockists</li><li>Privacy Policy</li><li>Terms &amp; Condition</li><li>Sitemap</li></ul></div>
  <div class="fcol" style="left:906px;top:76px;width:160px;line-height:18px"><h4>CONTACT DETAILS</h4>
    <div style="display:flex;gap:6px"><svg width="10" height="14" viewBox="0 0 10 14" style="flex:none;margin-top:3px"><path d="M5 0a5 5 0 015 5c0 4-5 9-5 9S0 9 0 5a5 5 0 015-5z" fill="#ddd"/><circle cx="5" cy="5" r="2" fill="#2e2e2e"/></svg><span>Lóuhólar 8, 108 Reykjavík, Vsk: 204118</span></div>
    <div style="margin-top:8px">☎ 555 0142</div>
    <div style="margin-top:8px">☎ 555 0142</div>
    <div style="margin-top:8px">✉ verk@vindurgata.is</div>
  </div>
  <div class="abs socials"><span></span><span></span><span></span><span></span><span></span></div>
</footer>
<div class="abs bottombar">Copyright © 2018 Vindurgata . All Rights Reserved.</div>

</body>
</html>
```